Personal training and nutrition business needs business card design

We need a business card that outlays our services and invites potential customers to join our team and take the first step to a healthier and more enjoyable life. We cater for any level of fitness and specialize in weight loss and conditioning, strength training, muscle gain and strength endurance. Whether you are just starting off or need some help getting to the next level of your journey we are here to get the job done.
We specialize in one on one or one on two personal training sessions and each program will be custom made to suit individual fitness goals of our clients

```html
<!DOCTYPE html>
<html lang="en">
<head>
<meta charset="utf-8">
<title>Stride &amp; Core — Business Card</title>
<link rel="stylesheet" href="https://fonts.googleapis.com/css2?family=Arimo:wght@400;700&family=Saira+Condensed:wght@500&display=swap">
<style>
  :root {
    --page: #161617;
    --card: #2f2f31;
    --card-deep: #262628;
    --purple: #9b5cc4;
    --purple-soft: #b46fd0;
    --violet: #6d3fc0;
    --ink: #ffffff;
    --ink-muted: #d9d9dc;
  }
  * { box-sizing: border-box; margin: 0; padding: 0; }
  html, body { width: 1200px; height: 900px; overflow: hidden; }
  body {
    background: var(--page);
    font-family: "Arimo", Arial, sans-serif;
    color: var(--ink);
    display: flex;
    flex-direction: column;
    align-items: center;
    justify-content: center;
    gap: 36px;
  }
  .card {
    position: relative;
    width: 700px;
    height: 400px;
    background: var(--card);
    overflow: hidden;
    border-bottom: 5px solid transparent;
    border-image: linear-gradient(90deg, var(--violet), var(--purple-soft)) 1;
    box-shadow: 0 12px 30px rgba(0,0,0,.55);
  }
  .card--back {
    background: linear-gradient(160deg, #3c3c3e 0%, var(--card) 45%, var(--card-deep) 100%);
  }
  .brand { position: absolute; }
  .brand__name {
    font-family: "Arimo", Arial, sans-serif;
    font-weight: 700;
    text-transform: uppercase;
    color: var(--ink);
    letter-spacing: 2px;
    line-height: .95;
    display: flex;
    align-items: center;
    gap: 14px;
  }
  .brand__dot {
    width: 18px; height: 18px; border-radius: 50%;
    background: var(--purple);
    flex: none;
  }
  .brand__tagline {
    font-family: "Saira Condensed", "Arial Narrow", sans-serif;
    font-weight: 500;
    text-transform: uppercase;
    color: var(--purple-soft);
    letter-spacing: 1.5px;
    margin-top: 8px;
  }
  .card--front .brand { left: 48px; top: 48px; }
  .card--front .brand__name { font-size: 38px; }
  .card--front .brand__tagline { font-size: 12px; padding-left: 32px; }

  .contacts {
    position: absolute; left: 48px; top: 190px;
    list-style: none;
    font-size: 20px;
    line-height: 1.55;
  }
  .contacts li { display: flex; align-items: center; gap: 12px; }
  .contacts svg { width: 16px; height: 16px; flex: none; }

  .person {
    position: absolute; right: 48px; top: 110px;
    text-align: right;
  }
  .person__name {
    font-weight: 700; font-size: 24px; text-transform: uppercase;
    color: var(--purple); letter-spacing: 1px;
  }
  .person__role { font-size: 20px; margin-top: 6px; }
  .person__address { font-size: 20px; margin-top: 14px; line-height: 1.3; font-style: normal; }

  .motto {
    position: absolute; right: 48px; bottom: 48px;
    font-size: 21px; color: var(--ink);
  }

  .card--back .brand { right: 56px; bottom: 52px; text-align: right; }
  .card--back .brand__name { font-size: 64px; justify-content: flex-end; }
  .card--back .brand__tagline { font-size: 15px; }
</style>
</head>
<body>

  <article class="card card--front">
    <div class="brand">
      <div class="brand__name"><span class="brand__dot"></span>Stride &amp; Core</div>
      <div class="brand__tagline">Personal training. Nutrition. Motivation</div>
    </div>

    <ul class="contacts">
      <li>
        <svg viewBox="0 0 16 16" aria-hidden="true"><path d="M4 1.5l2.2 3-1.3 1.6a9 9 0 0 0 5 5l1.6-1.3 3 2.2-1.4 2.4C7.5 14.6 1.4 8.5 1.6 2.9z" fill="var(--purple)"/></svg>
        555-014-2100
      </li>
      <li>
        <svg viewBox="0 0 16 16" aria-hidden="true"><rect x="1.5" y="3.5" width="13" height="9" fill="none" stroke="var(--purple)" stroke-width="1.5"/><path d="M1.5 3.5L8 9l6.5-5.5" fill="none" stroke="var(--purple)" stroke-width="1.5"/></svg>
        hello@strideandcore.net
      </li>
      <li>
        <svg viewBox="0 0 16 16" aria-hidden="true"><circle cx="8" cy="8" r="6.5" fill="none" stroke="var(--purple)" stroke-width="1.4"/><ellipse cx="8" cy="8" rx="2.8" ry="6.5" fill="none" stroke="var(--purple)" stroke-width="1.2"/><path d="M1.5 8h13M2.5 5h11M2.5 11h11" stroke="var(--purple)" stroke-width="1.1"/></svg>
        www.strideandcore.net
      </li>
    </ul>

    <div class="person">
      <div class="person__name">Daniel Reyes</div>
      <div class="person__role">Manager</div>
      <address class="person__address">Your address<br>city, state, ZIP 0000</address>
    </div>

    <p class="motto">Strong body, Strong mind</p>
  </article>

  <article class="card card--back">
    <div class="brand">
      <div class="brand__name">Stride<br>&amp; Core</div>
      <div class="brand__tagline">Personal training. Nutrition. Motivation</div>
    </div>
  </article>

</body>
</html>
```